Business Card for beauty technology startup

Design Glimora Business Card for a Beauty, based on the website identity and colors (https://www.glimora-example.com).
Glimora is a beauty tech startup that gathers helpful product info for beauty lovers and consumers (such as availability on stores, price range and product reviews) for makeup products. The card design must be young, colorful but clean, and very modern.

Target Market(s)

woman, 15-35

Industry/Entity Type

Cosmetics

Contact Information for Business Card

Full Name, address, phone

Font styles to use
Other font styles liked:
• Advent Pro

Colors
e34297
86cfc6
ffffff
5c5c5c
e8e8e8
e667a6
b2b2b2

Requirements
Must have
• One full colored side with a creative design and another with card info
• Use Color palette: #95C5C5 and/or #D38AA5
• Use fonts: Advent Pro
• Use website identity: https://www.glimora-example.com
Nice to have
• If needed extra font: Roboto

```html
<!DOCTYPE html>
<html lang="en">
<head>
<meta charset="utf-8">
<title>Glimora Business Card</title>
<link rel="stylesheet" href="https://fonts.googleapis.com/css2?family=Advent+Pro:wght@300;400&family=Roboto:wght@400;500&display=swap">
<style>
  :root {
    --stage: #2b2b2b;
    --rose: #b87f93;
    --paper: #f4f4f4;
    --white: #ffffff;
  }
  html, body { margin: 0; padding: 0; overflow: hidden; }
  body { width: 1200px; height: 960px; background: var(--stage); position: relative; font-family: "Roboto", sans-serif; }
  .card { position: absolute; width: 600px; height: 342px; border-radius: 22px; overflow: hidden; }
  .card-front { left: 314px; top: 113px; background: var(--paper); }
  .card-back { left: 311px; top: 472px; background: var(--rose); }
  .card-shape { position: absolute; inset: 0; }
  .brand-mark { position: absolute; left: 101px; top: 37px; width: 96px; height: 96px; border: 3px solid var(--rose); border-radius: 50%; box-sizing: border-box; }
  .wordmark { position: absolute; left: 0; width: 302px; top: 162px; text-align: center; font-family: "Advent Pro", sans-serif; font-weight: 300; font-size: 44px; letter-spacing: 5px; color: var(--rose); }
  .details { position: absolute; right: 38px; top: 0; text-align: right; color: var(--white); }
  .person-name { position: absolute; right: 0; top: 46px; white-space: nowrap; font-weight: 500; font-size: 20px; }
  .person-role { position: absolute; right: 0; top: 73px; white-space: nowrap; font-size: 14px; }
  .address { position: absolute; right: 0; top: 163px; white-space: nowrap; font-size: 14px; line-height: 19px; }
  .contact-list { position: absolute; right: 0; top: 210px; margin: 0; padding: 0; list-style: none; font-size: 14px; line-height: 19px; white-space: nowrap; }
  .contact-list li { display: flex; justify-content: flex-end; align-items: center; gap: 5px; }
  .contact-list svg { width: 13px; height: 13px; fill: var(--white); }
  .contact-list li span { margin-right: 0; }
  .back-badge { position: absolute; left: 208px; top: 76px; width: 184px; height: 184px; border: 5px solid var(--white); border-radius: 50%; box-sizing: border-box; display: flex; align-items: center; justify-content: center; font-family: "Advent Pro", sans-serif; font-weight: 400; font-size: 40px; color: var(--white); letter-spacing: 1px; }
  .back-url { position: absolute; left: 0; width: 600px; top: 294px; text-align: center; font-size: 14px; letter-spacing: 5px; color: var(--white); }
</style>
</head>
<body>
  <section class="card card-front">
    <svg class="card-shape" viewBox="0 0 600 342" aria-hidden="true">
      <path d="M322 0 C 346 150 290 290 150 342 L600 342 L600 0 Z" fill="var(--rose)"/>
      <circle cx="322" cy="16" r="13" fill="var(--rose)"/>
      <path d="M352 6 C 372 170 300 300 168 342" fill="none" stroke="var(--white)" stroke-width="1.6"/>
    </svg>
    <div class="brand-mark"></div>
    <div class="wordmark">GLIMORA</div>
    <div class="details">
      <div class="person-name">CLARA WHITFIELD</div>
      <div class="person-role">CEO/FOUNDER</div>
      <div class="address">1420 Willow Crest Road<br>Fairbanks, Alaska 34812</div>
      <ul class="contact-list">
        <li><span>555 210 4837</span><svg viewBox="0 0 16 16"><path d="M3 1 L6 1 L7 5 L5 6 C6 8 8 10 10 11 L11 9 L15 10 L15 13 C15 14 14 15 13 15 C6 15 1 10 1 3 C1 2 2 1 3 1 Z"/></svg></li>
        <li><span>555 318 6092</span><svg viewBox="0 0 16 16"><path d="M4 0 H12 V16 H4 Z M5.5 2 V12 H10.5 V2 Z M7 13.3 H9 V14.6 H7 Z" fill-rule="evenodd"/></svg></li>
        <li><span>555 742 1573</span><svg viewBox="0 0 16 16"><path d="M4 1 H12 V5 H4 Z M1 6 H15 V12 H12 V15 H4 V12 H1 Z M5 10 V14 H11 V10 Z" fill-rule="evenodd"/></svg></li>
        <li><span>info@glimora-example.com</span><svg viewBox="0 0 16 16"><path d="M1 3 H15 L8 9 Z M1 5 L8 11 L15 5 V13 H1 Z"/></svg></li>
        <li><span>www.glimora-example.com</span><svg viewBox="0 0 16 16"><circle cx="8" cy="8" r="7"/></svg></li>
      </ul>
    </div>
  </section>

  <section class="card card-back">
    <div class="back-badge">Glimora</div>
    <div class="back-url">www.glimora-example.com</div>
  </section>
</body>
</html>
```